Home Remodeler Needs a Website!

Single page (plus contact form) website for small home remodeling company. He's got a few pictures he'd like on the site and needs some basic text. He likes clean, simple designs and is "more traditional" in his stylistic preferences. Most of his business comes from word-of-mouth advertising and so the site is just something he needs for people to feel more comfortable with his business.

Target Market(s)

People who want to remodel their homes

Coding

Coded - Design and coding required

Number of Pages Required

2 page

Requirements
Must have
• Main page to include some or all of the attached images, contact page. Neutral colors. Old domain: lindcroftmeadowbuild.com New domain: qm-ventureworks.com You can pull text from the old site or update it.
Should not have
• No loud colors/loud visual elements

```html
<!DOCTYPE html>
<html lang="en">
<head>
<meta charset="utf-8">
<title>Lindcroft Meadow Homes</title>
<link href="https://fonts.googleapis.com/css2?family=Playfair+Display:wght@400;700&family=Ubuntu:wght@400&display=swap" rel="stylesheet">
<style>
:root{
  --navy:#1f2c50;
  --ink:#222;
  --white:#fff;
  --hero-a:#6b5e4e;
  --hero-b:#3c3a36;
}
*{margin:0;padding:0;box-sizing:border-box}
html,body{width:1200px;height:2822px;overflow:hidden;background:var(--white)}
body{position:relative;font-family:'Ubuntu',sans-serif;color:var(--ink)}
.abs{position:absolute}
.serif{font-family:'Playfair Display',serif}
.hero{left:0;top:0;width:1200px;height:617px;overflow:hidden}
.hero-photo{position:absolute;inset:0;background:linear-gradient(160deg,#8b8274 0%,var(--hero-a) 40%,var(--hero-b) 100%)}
.hero-title{left:0;width:1200px;top:245px;text-align:center;color:var(--white);font-weight:700;font-size:51px;letter-spacing:.5px}
.hero-arrow{top:266px;width:22px;height:22px}
.menu-icon{left:1040px;top:34px;width:35px;height:22px}
.center-line{left:599px;width:3px;top:447px;height:154px;background:var(--navy)}
.section-title{left:0;width:1200px;text-align:center;font-size:40px;font-weight:400;color:var(--ink);text-transform:uppercase}
.accent{height:4px;width:50px;background:var(--navy)}
.welcome-text{left:150px;width:900px;top:736px;text-align:center;font-size:15px;line-height:28px}
.band{left:0;width:1200px;background:var(--navy);color:var(--white)}
.tinker-title{left:123px;top:965px;font-size:39px;color:var(--white);text-transform:uppercase}
.tinker-text{left:123px;top:1030px;width:460px;font-size:14.6px;line-height:27.7px;color:var(--white)}
.frame{border:4px solid;border-radius:30px}
.photo{border-radius:24px;box-shadow:0 18px 30px rgba(0,0,0,.22)}
.package-list{left:660px;top:1542px;list-style:none}
.package-list li{height:44.4px;display:flex;align-items:center;font-size:16.8px;color:#222}
.package-list svg{width:18px;height:12px;margin-right:32px;margin-left:4px}
.service{width:200px;text-align:center;font-size:12.5px;line-height:16px;text-transform:uppercase;color:#222}
.service svg{display:block;margin:0 auto 26px;width:120px;height:110px}
.footer-title{left:0;width:1200px;top:2518px;text-align:center;color:var(--white);font-weight:700;font-size:51px}
.phones{left:0;width:1200px;top:2590px;text-align:center;color:var(--white);font-size:35px}
.phones span{margin:0 50px}
.copy{left:0;width:1200px;top:2758px;text-align:center;font-size:17px;color:#222}
</style>
</head>
<body>

<section class="abs hero">
  <div class="hero-photo" role="img" aria-label="Remodeled open kitchen and living area with wood floors and French doors"></div>
  <svg class="abs" style="left:0;top:0" width="1200" height="617" viewBox="0 0 1200 617">
    <path d="M0 580 Q600 380 1200 580 L1200 617 L0 617 Z" fill="var(--navy)"/>
    <path d="M0 617 Q600 420 1200 617 Z" fill="var(--white)"/>
  </svg>
  <svg class="abs menu-icon" viewBox="0 0 35 22"><g stroke="#fff" stroke-width="2"><line x1="6" y1="1" x2="35" y2="1"/><line x1="0" y1="11" x2="35" y2="11"/><line x1="6" y1="21" x2="35" y2="21"/></g></svg>
  <svg class="abs hero-arrow" style="left:193px" viewBox="0 0 22 22"><polyline points="14,3 6,11 14,19" fill="none" stroke="#fff" stroke-width="2.5"/></svg>
  <h1 class="abs serif hero-title">LINDCROFT MEADOW HOMES</h1>
  <svg class="abs hero-arrow" style="left:978px" viewBox="0 0 22 22"><polyline points="8,3 16,11 8,19" fill="none" stroke="#fff" stroke-width="2.5"/></svg>
</section>
<div class="abs center-line"></div>

<h2 class="abs serif section-title" style="top:668px">Welcome to Lindcroft Meadow Homes</h2>
<p class="abs welcome-text">When you want affordable, quality home construction services; think of us to do the job.<br>Since 1981 Gordon Ashby has built and remodeled over 400 homes and businesses. Let us be your contractor for the next project you start.When quality, value and personal attention to detail are important With over 20 years experience in residential and commercial construction, you can trust your project to Lindcroft Meadow Homes.</p>

<section class="abs band" style="top:903px;height:458px">
  <div class="abs accent" style="left:120px;top:36px;background:var(--white)"></div>
  <h2 class="abs serif tinker-title" style="top:62px">Don't Tinker Around</h2>
  <p class="abs tinker-text" style="top:127px">I have built my business with a partnership of clients, employees, subcontractors, suppliers and inspectors. Since each project is unique, this partnership brings creative ideas to your home.<br><br>I have deep "hands on" history in construction from foundations to final finishing touches.&nbsp; We cultivate suppliers who deliver quality materials on time and without damage.&nbsp; Our subcontractors are our friends and will become yours too. When called upon to explain their part of the process, they are glad to.&nbsp; Commercial and Residential Contracting</p>
  <div class="abs frame" style="left:654px;top:46px;width:450px;height:326px;border-color:var(--white)"></div>
  <div class="abs photo" role="img" aria-label="Remodeled bathroom with soaking tub, glass shower and tiled vanity" style="left:673px;top:64px;width:451px;height:328px;background:linear-gradient(135deg,#8fa2a6,#6d7a78 50%,#7a6248)"></div>
</section>

<div class="abs accent" style="left:575px;top:1387px"></div>
<h2 class="abs serif section-title" style="top:1410px">All in One Package</h2>
<div class="abs frame" style="left:142px;top:1502px;width:450px;height:326px;border-color:var(--navy)"></div>
<div class="abs photo" role="img" aria-label="Remodeled kitchen with stainless fridge, farmhouse sink and blue walls" style="left:122px;top:1519px;width:451px;height:328px;background:linear-gradient(135deg,#2e4a7a,#6e6a63 45%,#3a2e26)"></div>
<ul class="abs package-list">
  <li><svg viewBox="0 0 18 12"><g fill="none" stroke="#333" stroke-width="1.3"><line x1="0" y1="6" x2="17" y2="6"/><polyline points="11,1 17,6 11,11"/></g></svg>Pre Construction Consultation</li>
  <li><svg viewBox="0 0 18 12"><g fill="none" stroke="#333" stroke-width="1.3"><line x1="0" y1="6" x2="17" y2="6"/><polyline points="11,1 17,6 11,11"/></g></svg>New Construction</li>
  <li><svg viewBox="0 0 18 12"><g fill="none" stroke="#333" stroke-width="1.3"><line x1="0" y1="6" x2="17" y2="6"/><polyline points="11,1 17,6 11,11"/></g></svg>Remodeling / kitchens and baths</li>
  <li><svg viewBox="0 0 18 12"><g fill="none" stroke="#333" stroke-width="1.3"><line x1="0" y1="6" x2="17" y2="6"/><polyline points="11,1 17,6 11,11"/></g></svg>Additions</li>
  <li><svg viewBox="0 0 18 12"><g fill="none" stroke="#333" stroke-width="1.3"><line x1="0" y1="6" x2="17" y2="6"/><polyline points="11,1 17,6 11,11"/></g></svg>Porches and Decks</li>
  <li><svg viewBox="0 0 18 12"><g fill="none" stroke="#333" stroke-width="1.3"><line x1="0" y1="6" x2="17" y2="6"/><polyline points="11,1 17,6 11,11"/></g></svg>Specializing in historic renovations.</li>
</ul>

<div class="abs accent" style="left:575px;top:1901px"></div>
<h2 class="abs serif section-title" style="top:1924px">Our Services</h2>

<div class="abs service" style="left:120px;top:2016px">
  <svg viewBox="0 0 120 110"><path d="M30 15 Q60 -5 95 10 Q115 40 100 85 Q70 108 35 95 Q10 60 30 15Z" fill="var(--navy)"/><g fill="none" stroke="#fff" stroke-width="3"><polyline points="5,55 60,22 115,55"/><line x1="20" y1="55" x2="100" y2="55"/></g></svg>Roofing
</div>
<div class="abs service" style="left:361px;top:2016px">
  <svg viewBox="0 0 120 110"><path d="M25 10 Q70 -5 105 20 Q115 60 95 100 Q55 110 25 95 Q10 50 25 10Z" fill="var(--navy)"/><g fill="none" stroke="#fff" stroke-width="3"><rect x="30" y="20" width="60" height="70"/><line x1="60" y1="20" x2="60" y2="90"/></g></svg>Window<br>Replacement
</div>
<div class="abs service" style="left:630px;top:2016px">
  <svg viewBox="0 0 120 110"><path d="M40 10 Q80 0 105 40 Q115 85 80 100 Q40 108 15 85 Q10 40 40 10Z" fill="var(--navy)"/><g fill="none" stroke="#fff" stroke-width="3"><polygon points="60,15 105,92 15,92"/><polyline points="64,40 54,64 66,64 56,84"/></g></svg>Electrical
</div>
<div class="abs service" style="left:890px;top:2016px">
  <svg viewBox="0 0 120 110"><path d="M30 15 Q75 -2 110 25 Q115 70 90 100 Q45 110 15 85 Q10 45 30 15Z" fill="var(--navy)"/><g fill="none" stroke="#fff" stroke-width="3"><rect x="15" y="25" width="90" height="45" rx="6"/><line x1="25" y1="58" x2="95" y2="58"/><path d="M45 80 q4 10 0 18 M60 80 q4 10 0 18 M75 80 q4 10 0 18"/></g></svg>Air<br>Conditioning
</div>

<div class="abs service" style="left:113px;top:2229px">
  <svg viewBox="0 0 120 110"><path d="M30 10 Q80 -2 110 30 Q115 80 85 100 Q40 108 15 80 Q8 40 30 10Z" fill="var(--navy)"/><g fill="none" stroke="#fff" stroke-width="3"><polyline points="20,50 60,18 100,50"/><rect x="32" y="48" width="56" height="45"/><rect x="52" y="68" width="16" height="25"/><line x1="5" y1="95" x2="115" y2="95"/></g></svg>Plumbing<br>Upgrades
</div>
<div class="abs service" style="left:361px;top:2229px">
  <svg viewBox="0 0 120 110"><path d="M35 15 Q80 0 110 35 Q115 80 80 100 Q40 105 20 80 Q10 45 35 15Z" fill="var(--navy)"/><g fill="none" stroke="#fff" stroke-width="3"><rect x="45" y="10" width="60" height="25" rx="6" transform="rotate(40 75 22)"/><line x1="50" y1="60" x2="15" y2="100"/></g></svg>Painting
</div>
<div class="abs service" style="left:630px;top:2229px">
  <svg viewBox="0 0 120 110"><path d="M25 15 Q70 -2 105 25 Q115 75 85 100 Q40 108 15 80 Q8 45 25 15Z" fill="var(--navy)"/><g fill="none" stroke="#fff" stroke-width="3"><rect x="5" y="10" width="110" height="92"/><line x1="60" y1="10" x2="60" y2="102"/><line x1="15" y1="56" x2="50" y2="56"/><polyline points="42,48 50,56 42,64"/><line x1="105" y1="56" x2="70" y2="56"/><polyline points="78,48 70,56 78,64"/></g></svg>Gutters
</div>
<div class="abs service" style="left:890px;top:2229px">
  <svg viewBox="0 0 120 110"><path d="M30 15 Q75 0 108 30 Q115 80 85 100 Q40 108 12 80 Q8 40 30 15Z" fill="var(--navy)"/><g fill="none" stroke="#fff" stroke-width="3"><rect x="5" y="20" width="110" height="80"/><line x1="60" y1="20" x2="60" y2="100"/><line x1="60" y1="40" x2="115" y2="40"/><line x1="60" y1="60" x2="115" y2="60"/><line x1="60" y1="80" x2="115" y2="80"/></g></svg>Concrete<br>Work
</div>

<section class="abs band" style="top:2444px;height:270px">
  <div class="abs accent" style="left:575px;top:48px;background:var(--white)"></div>
</section>
<h2 class="abs serif footer-title">LINDCROFT MEADOW HOMES</h2>
<p class="abs serif phones"><span>615-555-0142</span>|<span>615-555-0187</span></p>

<p class="abs copy">© 2021&nbsp; |&nbsp; www.companyname.com</p>

</body>
</html>
```